Business Card for Vorla Parts Wholesale supplier

Hi There! I need a new business card for our company. We are specialized in selling Vorla parts, mostly we sell new LCD screens for Zelnar and Drelks. I would like to see that back in the design.

You can find the colors and logo's on our website: www.hartuvo.nl

Industry/Entity Type

Business

Contact Information for Business Card

My Details:
Tobias Lindqvist

Phone: 0031687203316
E-mail: Tobias@hartuvo.nl

Slogan: "Because Quality Matters"

Font styles to use
Sans Serif

Colors

Designer to choose colors to be used in the design.

Requirements
Must have
• A Black backside with the Hartuvo logo on it. The front side should be clean with only my contact details.
• But I'm also open for something really different or awesome!
Nice to have
• Remember that we are in the parts & repairing industry, So i'll be handing those business cards mainly to repair companies. Maybe you can do something with that thought :)

```html
<!DOCTYPE html>
<html lang="en">
<head>
<meta charset="UTF-8">
<title>Hartuvo Business Card</title>
<link href="https://fonts.googleapis.com/css2?family=Oswald:wght@500&family=Work+Sans:wght@400;600&display=swap" rel="stylesheet">
<style>
  :root {
    --page-bg: #e4e6e8;
    --card-bg: #1b1c1e;
    --ink-light: #ffffff;
    --accent-orange: #f7941d;
    --card-shadow: rgba(0, 0, 0, 0.25);
  }
  * { margin: 0; padding: 0; box-sizing: border-box; }
  html, body {
    width: 1200px;
    height: 1000px;
    overflow: hidden;
    background: var(--page-bg);
  }
  .canvas {
    width: 1200px;
    height: 1000px;
    display: flex;
    flex-direction: column;
    align-items: center;
    justify-content: center;
    gap: 60px;
  }
  .card {
    width: 700px;
    height: 400px;
    background: var(--card-bg);
    border-radius: 4px;
    box-shadow: 0 14px 36px var(--card-shadow);
    display: flex;
    flex-direction: column;
    align-items: center;
    justify-content: center;
  }
  .brand {
    display: flex;
    align-items: center;
    gap: 16px;
  }
  .brand-dot {
    width: 44px;
    height: 44px;
    border-radius: 50%;
    background: var(--ink-light);
  }
  .brand-name {
    font-family: "Work Sans", sans-serif;
    font-weight: 600;
    font-size: 58px;
    color: var(--ink-light);
    letter-spacing: 0.5px;
  }
  .holder-name {
    font-family: "Oswald", sans-serif;
    font-weight: 500;
    font-size: 30px;
    color: var(--accent-orange);
    text-transform: uppercase;
    letter-spacing: 0.5px;
  }
  .divider {
    width: 28px;
    height: 2px;
    background: var(--ink-light);
    margin: 14px 0 14px;
  }
  .contact-line {
    font-family: "Work Sans", sans-serif;
    font-weight: 400;
    font-size: 15px;
    color: var(--ink-light);
    letter-spacing: 0.6px;
  }
  .slogan {
    font-family: "Work Sans", sans-serif;
    font-weight: 600;
    font-size: 15px;
    color: var(--ink-light);
    letter-spacing: 0.6px;
    margin-top: 8px;
  }
</style>
</head>
<body>
  <main class="canvas">
    <section class="card card-logo-side">
      <div class="brand">
        <span class="brand-dot"></span>
        <span class="brand-name">hartuvo</span>
      </div>
    </section>
    <section class="card card-contact-side">
      <h1 class="holder-name">Tobias Lindqvist</h1>
      <div class="divider"></div>
      <p class="contact-line">P: 0031687203316 | E: Tobias@hartuvo.nl | www.hartuvo.nl</p>
      <p class="slogan">Because Quality Matters</p>
    </section>
  </main>
</body>
</html>
```